Professional Engineering Web Design

Project Brief: Website Redesign for Mechanical Design Consultancy
Project Overview
I want to update and improve my current website to create a more professional, modern, and high-credibility online presence for my mechanical design consultancy.

Current site: https://valtorix.design/

The new website must communicate expertise, precision, and trust—matching the standard of top engineering and product design agencies.

Reference Websites (Style + Structure Inspiration)
These represent the quality, cleanliness, and professionalism I want to achieve:

https://plinthwaredesign.com/
https://www.sorvane.com/
https://bramlow-uk.com/
Brand Look
Professional, modern, engineering-focused aesthetic
Clean layouts and strong typography
High-quality imagery conveying precision, innovation, and mechanical expertise
Colour scheme and styling must follow my existing logo (attached in project)
Platform Requirements
The website must be built on WordPress
Should use a clean, flexible theme or modern page builder (Elementor, Gutenberg, Bricks, or similar)
Avoid overly complex custom coding so I can easily edit content later
Final deliverable must allow me to manage and update content without developer assistance
Functionality
Fast-loading, lightweight, and smooth user experience
Clean animations and transitions similar to the reference sites
Fully mobile responsive
Clear navigation and strong visual hierarchy
Contact forms optimised for lead generation
Optional: subtle scroll effects, case study sliders, icon animations, etc.
SEO Aspirations
Developer should recommend and implement a modern SEO strategy
Proper on-page SEO setup (titles, meta, schema, alt tags, heading structure)
Optimised site architecture for ranking and crawling
Aim: Generate leads through improved visibility and keyword targeting
Optional but useful: Google Analytics, Google Search Console setup
User Journeys
(Recommended structure)

The site should be crafted around clear, intuitive journeys for each type of visitor:

Potential new clients
Quickly understand what services I offer
View examples of past work / case studies
See credibility indicators (process, expertise, industries served)
Easily contact me or request a project discussion
Returning clients
Access updated portfolio items
Find contact details or book follow-up work easily
General visitors discovering through SEO
Be guided to valtorix service areas
Understand my value proposition quickly
Be invited to learn more or make contact
The developer should design the structure to support these journeys smoothly.

Maintenance Expectations
Website will be maintained by me, so it should be easy to update using relatively basic WordPress skills
Use modular templates and simple backend structure
Avoid unnecessary plugins
Provide brief handover documentation if required
Hosting Preferences
Site is currently hosted via a family member
Open to discussing moving to a paid, reliable hosting provider if preferable for performance and maintainability
Developer may advise on the best hosting setup for WordPress
Content
Most content can be taken from the existing website
Developer is welcome to suggest improvements to structure, layout, and imagery
Must remain easy for me to edit or add new content later (e.g., new projects)
Deliverables
Fully built WordPress website
Clean, professional, modern design inspired by the reference sites
Mobile-responsive across all devices
SEO-ready structure and optimisations
Transfer of website and admin rights
Any design assets, templates, or documentation used

```html
<!DOCTYPE html>
<html lang="en">
<head>
<meta charset="utf-8">
<title>Valtorix Design — Precision Mechanical &amp; Product Design</title>
<link href="https://fonts.googleapis.com/css2?family=Plus+Jakarta+Sans:wght@400;500;600;700;800&display=swap" rel="stylesheet">
<style>
:root{
  --blue:#2f57ef;
  --blue-deep:#1e3fd6;
  --blue-soft:#e9eefd;
  --ink:#1c1e24;
  --text:#3b3f4a;
  --muted:#6b7080;
  --white:#ffffff;
  --dark:#1b1c20;
  --line:#d7ddf3;
}
*{box-sizing:border-box;margin:0;padding:0}
html,body{width:1200px;height:4518px;overflow:hidden}
body{position:relative;font-family:"Plus Jakarta Sans",sans-serif;color:var(--ink);background:var(--blue-soft)}
.abs{position:absolute}
.btn{position:absolute;display:flex;align-items:center;justify-content:space-between;height:36px;padding:0 4px 0 20px;border-radius:18px;background:var(--blue);color:var(--white);font-size:12px;font-weight:600}
.btn.light{background:var(--white);color:var(--blue)}
.btn .dot{width:28px;height:28px;border-radius:50%;background:var(--white);display:flex;align-items:center;justify-content:center}
.btn.light .dot{background:var(--blue)}
.btn .dot svg{width:14px;height:14px}

/* hero */
.hero{position:absolute;left:0;top:0;width:1200px;height:620px;overflow:hidden}
.hero-photo{position:absolute;inset:0;background:linear-gradient(120deg,#2a2c31 0%,#3b3d42 45%,#24262b 100%)}
.hero-curve{position:absolute;left:0;top:0}
.nav{position:absolute;top:24px;left:120px;width:960px;height:38px;display:flex;align-items:center}
.logo{display:flex;align-items:center;gap:8px;color:var(--white);font-size:26px;font-weight:600;letter-spacing:3px}
.logo .mark{width:34px;height:34px;border-radius:50%;background:var(--blue)}
.menu{display:flex;gap:28px;margin-left:52px;font-size:12px;font-weight:600;color:var(--white)}
.menu .on{color:#6f8dff}
.nav-phone{margin-left:auto;display:flex;align-items:center;gap:8px;color:var(--white);font-size:15px;font-weight:600}
.ico-phone{width:24px;height:24px;border-radius:50%;border:2px solid var(--blue);display:flex;align-items:center;justify-content:center}
.nav .btn{position:relative;margin-left:24px;height:32px;font-size:11px;padding-left:14px;width:118px}
.nav .btn .dot{width:24px;height:24px}
.hero h1{position:absolute;left:118px;top:142px;color:var(--white);font-size:58px;line-height:61px;font-weight:800;letter-spacing:.5px}
.hero h1 span{color:var(--blue)}
.hero p{position:absolute;left:120px;top:338px;width:380px;color:#e5e7ee;font-size:12px;line-height:18px}
.hero-disc{position:absolute;left:666px;top:130px;width:336px;height:336px;border-radius:50%;background:var(--blue)}
.hero-monitor{position:absolute;left:672px;top:180px;width:340px;height:290px;border-radius:12px;background:linear-gradient(160deg,#f4f6fa,#b9bec8)}

/* about */
.about-ring{position:absolute;left:120px;top:668px;width:400px;height:400px;border-radius:50%;border:14px solid #dde4fb}
.about-portrait{position:absolute;left:152px;top:700px;width:336px;height:336px;border-radius:50%;background:linear-gradient(150deg,#6f7a86,#3b4653);border:8px solid var(--white)}
.about-wheel{position:absolute;left:352px;top:872px;width:172px;height:172px;border-radius:50%;background:radial-gradient(circle,#e8eaee 0%,#9ea3ab 60%,#5d626a 100%)}
.about h2{position:absolute;left:592px;top:706px;font-size:38px;line-height:44px;font-weight:700}
.about h2 span{color:var(--blue)}
.about .copy{position:absolute;left:592px;top:806px;width:470px;font-size:11.5px;line-height:18px;color:var(--text)}
.about .copy p+p{margin-top:14px}
.about .phone{position:absolute;left:798px;top:984px;display:flex;align-items:center;gap:8px;font-size:15px;font-weight:600}
.about .sep{position:absolute;left:782px;top:978px;width:1px;height:40px;background:var(--line)}

.features{position:absolute;left:128px;top:1096px;display:flex;gap:35px}
.feature{width:290px;height:144px;background:var(--white);border:1px solid var(--line);border-radius:6px;display:flex;flex-direction:column;align-items:center;padding-top:26px}
.feature .ico{width:56px;height:56px;border-radius:50%;border:2px solid var(--blue);display:flex;align-items:center;justify-content:center}
.feature .ico i{width:44px;height:44px;border-radius:50%;background:var(--blue);display:flex;align-items:center;justify-content:center}
.feature h3{margin-top:18px;font-size:14px;font-weight:700}

.watermark{position:absolute;left:0;width:1200px;font-size:104px;font-weight:700;color:transparent;-webkit-text-stroke:1.5px #ffffff;white-space:nowrap;overflow:hidden;letter-spacing:2px}

/* services */
.services{position:absolute;left:0;top:1363px;width:1200px;height:546px;background:radial-gradient(ellipse at 60% 40%,#4a6cff 0%,#2d52ef 45%,#1d3ed8 100%)}
.services h2{position:absolute;top:44px;width:100%;text-align:center;color:var(--white);font-size:36px;font-weight:700}
.svc{position:absolute;top:110px;width:240px;text-align:center;color:var(--white)}
.svc .pic{margin:0 auto;width:196px;height:196px;border-radius:50%;border:6px solid var(--white);background:linear-gradient(150deg,#d9dde6,#7d8696)}
.svc .badge{margin:-38px auto 0;position:relative;width:50px;height:50px;border-radius:50%;background:var(--white);border:3px solid var(--blue);display:flex;align-items:center;justify-content:center}
.svc h3{margin-top:16px;font-size:15px;font-weight:700}
.svc p{margin-top:8px;font-size:11px;line-height:15px;color:#dfe6ff}
.arrow{position:absolute;top:200px;width:20px;height:20px;border-radius:50%;border:1.5px solid #c9d4ff}

/* portfolio */
.section-title{position:absolute;width:1200px;text-align:center;font-size:36px;font-weight:700}
.work{position:absolute;top:2019px;height:323px;border-radius:4px}

/* process */
.step{position:absolute;top:2464px;width:168px;height:170px}
.step .arc{position:absolute;left:0;top:24px;width:168px;height:168px;border-radius:50%;border:2px solid #c9d3f6;border-top-color:transparent;border-left-color:#c9d3f6;background:linear-gradient(180deg,rgba(255,255,255,0) 40%,rgba(255,255,255,.7))}
.step .num{position:absolute;left:62px;top:0;width:44px;height:44px;border-radius:50%;background:var(--white);border:2px solid var(--blue);display:flex;align-items:center;justify-content:center;font-size:16px;font-weight:700;color:var(--blue)}
.step .stem{position:absolute;left:83px;top:46px;width:2px;height:30px;background:var(--blue)}
.step h4{position:absolute;top:106px;width:100%;text-align:center;font-size:15px;font-weight:700;line-height:18px}

/* blog */
.blog-band{position:absolute;left:0;top:2772px;width:1200px;height:570px;background:#e6ebfc}
.post{position:absolute;top:2885px;width:307px;height:325px;background:var(--white);border-radius:4px;padding:16px}
.post .pic{height:212px;background:linear-gradient(150deg,#8791a2,#2b3140)}
.post .date{margin-top:14px;font-size:9.5px;color:var(--blue);font-weight:600;text-decoration:underline}
.post h3{margin-top:8px;width:250px;font-size:14px;line-height:18px;font-weight:600}
.post .go{position:absolute;right:12px;bottom:12px;width:20px;height:20px;border-radius:50%;background:var(--blue);display:flex;align-items:center;justify-content:center}

/* contact */
.contact-band{position:absolute;left:0;top:3342px;width:1200px;height:700px;background:#f2f5fe}
.form{position:absolute;left:121px;top:3376px;width:470px;height:386px;background:var(--white);border-radius:4px;box-shadow:0 2px 10px rgba(30,50,120,.08)}
.form h2{margin:0 8px;height:60px;background:#2a2c31;color:var(--white);border-radius:4px;font-size:36px;font-weight:700;display:flex;align-items:center;justify-content:center}
.field{position:absolute;height:38px;border:1px solid #bfc4cf;font-size:11px;color:#555a66;padding:10px 12px}
.map-ring{position:absolute;left:682px;top:3394px;width:370px;height:370px;border-radius:50%;border:14px solid #dde4fb}
.map{position:absolute;left:708px;top:3420px;width:318px;height:318px;border-radius:50%;background:linear-gradient(135deg,#eef1e8 0%,#dfe6d6 55%,#9fd0ea 100%)}
.car{position:absolute;left:670px;top:3650px;width:340px;height:120px;border-radius:40px 60px 20px 20px;background:linear-gradient(180deg,#e6e8ec,#9da2aa)}

/* cta + footer */
.footer{position:absolute;left:0;top:4030px;width:1200px;height:488px;background:var(--dark)}
.cta{position:absolute;left:123px;top:3920px;width:954px;height:264px;border-radius:132px;background:var(--blue)}
.cta-pic{position:absolute;left:160px;top:3950px;width:240px;height:200px;border-radius:16px;background:linear-gradient(150deg,#eeeef0,#3b3e46)}
.cta h2{position:absolute;left:543px;top:3972px;color:var(--white);font-size:38px;line-height:42px;font-weight:700}
.cta-text{position:absolute;left:543px;top:4058px;width:400px;color:#e4e9ff;font-size:11.5px;line-height:16px}
.f-logo{position:absolute;left:123px;top:4232px}
.f-about{position:absolute;left:123px;top:4288px;width:190px;color:#c6c8ce;font-size:9px;line-height:16px}
.f-col{position:absolute;top:4240px;color:var(--white)}
.f-col h4{font-size:14px;font-weight:700;margin-bottom:12px}
.f-col li{list-style:none;font-size:9px;color:#c6c8ce;line-height:21px;display:flex;align-items:center;gap:8px}
.f-col .ci{width:22px;height:22px;border-radius:50%;border:1.5px solid #fff;display:flex;align-items:center;justify-content:center;flex-shrink:0}
.f-col .ci i{width:6px;height:6px;border-radius:50%;background:#fff}
.f-col.contact li{line-height:34px}
.f-col.brands li{line-height:34px}
.vline{position:absolute;top:4236px;width:1px;height:170px;background:#3a3c43}
.f-rule{position:absolute;left:123px;top:4426px;width:954px;height:1px;background:#3a3c43}
.copyright{position:absolute;left:0;top:4442px;width:1200px;text-align:center;color:#c6c8ce;font-size:9px}
</style>
</head>
<body>

<!-- hero -->
<header class="hero">
  <div class="hero-photo" role="img" aria-label="Dark photograph of a classic saloon car parked outdoors"></div>
  <svg class="hero-curve" width="1200" height="620" viewBox="0 0 1200 620">
    <path d="M0 620 L0 505 Q600 720 1200 480 L1200 620 Z" fill="#e9eefd"/>
    <path d="M0 505 Q600 720 1100 530 L1090 560 Q600 740 0 545 Z" fill="#2f57ef"/>
    <path d="M1100 530 Q1160 505 1200 480 L1200 500 Q1160 525 1108 548 Z" fill="#2b2d33"/>
  </svg>
  <nav class="nav">
    <div class="logo"><span class="mark"></span>valtorix</div>
    <div class="menu"><span class="on">Home</span><span>About Us</span><span>Our Services</span><span>Portfolio</span><span>Case Studies</span></div>
    <div class="nav-phone"><span class="ico-phone"><svg width="12" height="12" viewBox="0 0 24 24"><path d="M6.6 10.8a15 15 0 006.6 6.6l2.2-2.2c.3-.3.7-.4 1-.2 1.1.4 2.3.6 3.6.6.6 0 1 .4 1 1V20c0 .6-.4 1-1 1A17 17 0 013 4c0-.6.4-1 1-1h3.5c.6 0 1 .4 1 1 0 1.3.2 2.5.6 3.6.1.3 0 .7-.2 1z" fill="#fff"/></svg></span>+44 (0) 7700 900418</div>
    <div class="btn">Contact Us<span class="dot"><svg viewBox="0 0 24 24"><path d="M5 12h14M13 6l6 6-6 6" stroke="#2f57ef" stroke-width="3" fill="none"/></svg></span></div>
  </nav>
  <h1>Precision<br>Mechanical &amp;<br>Product <span>Design</span></h1>
  <p>UK-based mechanical and product design consultancy delivering complete solutions from concept to full-scale production.</p>
  <div class="btn" style="left:120px;top:402px;width:140px">Get Started<span class="dot"><svg viewBox="0 0 24 24"><path d="M5 12h14M13 6l6 6-6 6" stroke="#2f57ef" stroke-width="3" fill="none"/></svg></span></div>
  <div class="hero-disc"></div>
  <div class="hero-monitor" role="img" aria-label="Illustration of a monitor with an exploded gear assembly bursting from the screen"></div>
</header>

<!-- about -->
<section class="about">
  <div class="about-ring"></div>
  <div class="about-portrait" role="img" aria-label="Portrait photograph of the chief engineer"></div>
  <div class="about-wheel" role="img" aria-label="Photograph of a polished alloy wheel"></div>
  <h2>About Valtorix<br><span>Design.</span></h2>
  <div class="copy">
    <p>Welcome to Valtorix Design. We are a UK based design consultancy offering a comprehensive mechanical and product design service from initial concepts through to full volume production.</p>
    <p>Elliot Marsh is the Chief Engineer at Valtorix Design. He has <b>11 years experience</b> working as a mechanical design engineer in multiple industries including <b>high performance automotive, consumer products, medical, industrial plus</b> many more. He has worked in multiple roles across a wide range of projects.</p>
  </div>
  <div class="btn" style="left:590px;top:980px;width:178px">Read More About Us<span class="dot"><svg viewBox="0 0 24 24"><path d="M5 12h14M13 6l6 6-6 6" stroke="#2f57ef" stroke-width="3" fill="none"/></svg></span></div>
  <div class="sep"></div>
  <div class="phone"><span class="ico-phone"><svg width="12" height="12" viewBox="0 0 24 24"><path d="M6.6 10.8a15 15 0 006.6 6.6l2.2-2.2c.3-.3.7-.4 1-.2 1.1.4 2.3.6 3.6.6.6 0 1 .4 1 1V20c0 .6-.4 1-1 1A17 17 0 013 4c0-.6.4-1 1-1h3.5c.6 0 1 .4 1 1 0 1.3.2 2.5.6 3.6.1.3 0 .7-.2 1z" fill="#2f57ef"/></svg></span>+44 (0) 7700 900418</div>

  <div class="features">
    <div class="feature"><span class="ico"><i><svg width="22" height="22" viewBox="0 0 24 24" fill="none" stroke="#fff" stroke-width="1.8"><path d="M12 2l9 5v10l-9 5-9-5V7z"/><path d="M3 7l9 5 9-5M12 12v10"/></svg></i></span><h3>Bespoke Product Design</h3></div>
    <div class="feature"><span class="ico"><i><svg width="22" height="22" viewBox="0 0 24 24" fill="none" stroke="#fff" stroke-width="1.8"><rect x="7" y="3" width="10" height="8"/><rect x="2" y="13" width="9" height="8"/><rect x="13" y="13" width="9" height="8"/></svg></i></span><h3>3D Modelling and Drawings</h3></div>
    <div class="feature"><span class="ico"><i><svg width="22" height="22" viewBox="0 0 24 24" fill="none" stroke="#fff" stroke-width="1.8"><path d="M3 21h18M5 21V11l5 3V11l5 3V7h4v14"/></svg></i></span><h3>Design for Manufacture</h3></div>
  </div>
</section>

<div class="watermark" style="top:1262px">Valtorix Design Valtorix</div>

<!-- services -->
<section class="services">
  <h2>Our Services</h2>
  <span class="arrow" style="left:92px"></span>
  <span class="arrow" style="left:1086px"></span>
  <div class="svc" style="left:113px"><div class="pic" role="img" aria-label="Photograph of CAD software on twin monitors"></div><div class="badge"><svg width="20" height="20" viewBox="0 0 24 24" fill="none" stroke="#2f57ef" stroke-width="2"><path d="M12 2l9 5v10l-9 5-9-5V7z"/></svg></div><h3>Design Consultancy</h3><p>If you've got a great idea and want to begin developing it but don't know where to start, we can help.</p></div>
  <div class="svc" style="left:357px"><div class="pic" role="img" aria-label="Photograph of a hand sketching a technical drawing"></div><div class="badge"><svg width="20" height="20" viewBox="0 0 24 24" fill="none" stroke="#2f57ef" stroke-width="2"><circle cx="12" cy="12" r="4"/><circle cx="12" cy="12" r="9"/></svg></div><h3>Mechanical Design</h3><p>Our primary service is mechanical design service from initial concepts through to production manufacture.</p></div>
  <div class="svc" style="left:601px"><div class="pic" role="img" aria-label="Photograph of a blue 3D printed wheel part" style="background:radial-gradient(circle,#7fb2ff,#1838c8)"></div><div class="badge"><svg width="20" height="20" viewBox="0 0 24 24" fill="none" stroke="#2f57ef" stroke-width="2"><rect x="4" y="4" width="16" height="16"/></svg></div><h3>3D Printing</h3><p>We can manufacture low volume functional prototypes using 3D printing.</p></div>
  <div class="svc" style="left:845px"><div class="pic" role="img" aria-label="Photograph of a team meeting around a whiteboard"></div><div class="badge"><svg width="20" height="20" viewBox="0 0 24 24" fill="none" stroke="#2f57ef" stroke-width="2"><path d="M12 3l9 5-9 5-9-5zM3 13l9 5 9-5"/></svg></div><h3>Project Management</h3><p>We have worked on hundreds of projects over the years - from very small to projects that span many years.</p></div>
  <div class="btn light" style="left:520px;top:450px;width:160px">View All Services<span class="dot"><svg viewBox="0 0 24 24"><path d="M5 12h14M13 6l6 6-6 6" stroke="#fff" stroke-width="3" fill="none"/></svg></span></div>
</section>

<!-- portfolio -->
<div class="section-title" style="top:1952px;background:none">Our Portfolio</div>
<div class="abs" style="left:0;top:1909px;width:1200px;height:480px;background:var(--white);z-index:-1"></div>
<div class="work" style="left:0;width:65px;background:linear-gradient(150deg,#bfc3ca,#6b7078)" role="img" aria-label="Portfolio photograph"></div>
<div class="work" style="left:72px;width:345px;background:linear-gradient(150deg,#9aa0a8,#4e545c)" role="img" aria-label="Photograph of a machined gearbox casing"></div>
<div class="work" style="left:424px;width:344px;background:linear-gradient(160deg,#f2f2f3,#cfd1d5)" role="img" aria-label="Render of a kart chassis with steering wheel"></div>
<div class="work" style="left:775px;width:344px;background:radial-gradient(circle,#6b7078,#2d3036 70%,#c9c6bd)" role="img" aria-label="Photograph of a planetary gear set"></div>
<div class="work" style="left:1126px;width:74px;background:linear-gradient(150deg,#c8cbd0,#8e939a)" role="img" aria-label="Portfolio photograph"></div>

<!-- process -->
<div class="section-title" style="top:2388px">Our Process</div>
<div class="step" style="left:123px"><div class="arc"></div><div class="stem"></div><div class="num">01</div><h4>Discovery</h4></div>
<div class="step" style="left:316px"><div class="arc"></div><div class="stem"></div><div class="num">02</div><h4>Concept</h4></div>
<div class="step" style="left:518px"><div class="arc"></div><div class="stem"></div><div class="num">03</div><h4>Detailed<br>Design</h4></div>
<div class="step" style="left:719px"><div class="arc"></div><div class="stem"></div><div class="num">04</div><h4>Prototype</h4></div>
<div class="step" style="left:907px"><div class="arc"></div><div class="stem"></div><div class="num">05</div><h4>Production<br>Launch</h4></div>

<div class="watermark" style="top:2672px;left:48px">Valtorix Design Valtorix</div>

<!-- blog -->
<div class="blog-band"></div>
<div class="section-title" style="top:2818px">Latest Blog</div>
<article class="post" style="left:121px"><div class="pic" role="img" aria-label="Photograph of CAD models on computer screens"></div><div class="date">November 15, 2022, Read</div><h3>Designing for Manufacture: How to Reduce Cost &amp; Lead Time</h3><span class="go"><svg width="10" height="10" viewBox="0 0 24 24"><path d="M5 12h14M13 6l6 6-6 6" stroke="#fff" stroke-width="3" fill="none"/></svg></span></article>
<article class="post" style="left:447px"><div class="pic" role="img" aria-label="Photograph of a hand drawing technical plans" style="background:linear-gradient(150deg,#f0f0f0,#9b9ea4)"></div><div class="date">November 15, 2022, Read</div><h3>The Role of Tolerance Analysis in High-Precision Engineering</h3><span class="go"><svg width="10" height="10" viewBox="0 0 24 24"><path d="M5 12h14M13 6l6 6-6 6" stroke="#fff" stroke-width="3" fill="none"/></svg></span></article>
<article class="post" style="left:773px"><div class="pic" role="img" aria-label="Photograph of a 3D printer head under purple light" style="background:linear-gradient(150deg,#7b3fd6,#1e2a3a 60%,#38c08a)"></div><div class="date">November 15, 2022, Read</div><h3>How to Prepare a Supplier Ready Engineering Package</h3><span class="go"><svg width="10" height="10" viewBox="0 0 24 24"><path d="M5 12h14M13 6l6 6-6 6" stroke="#fff" stroke-width="3" fill="none"/></svg></span></article>
<div class="btn" style="left:528px;top:3245px;width:144px">View All Blog<span class="dot"><svg viewBox="0 0 24 24"><path d="M5 12h14M13 6l6 6-6 6" stroke="#2f57ef" stroke-width="3" fill="none"/></svg></span></div>

<!-- contact -->
<div class="contact-band"></div>
<form class="form">
  <h2 style="margin-top:10px">Let's Work Together.</h2>
  <div class="field" style="left:14px;top:98px;width:218px">Frist Name*</div>
  <div class="field" style="left:238px;top:98px;width:218px">Last Name*</div>
  <div class="field" style="left:14px;top:142px;width:218px">Email*</div>
  <div class="field" style="left:238px;top:142px;width:218px">Phone*</div>
  <div class="field" style="left:14px;top:186px;width:442px;height:100px">Mesage*</div>
  <div class="btn" style="left:146px;top:316px;width:180px">Submit<span class="dot"><svg viewBox="0 0 24 24"><path d="M5 12h14M13 6l6 6-6 6" stroke="#2f57ef" stroke-width="3" fill="none"/></svg></span></div>
</form>
<div class="map-ring"></div>
<div class="map" role="img" aria-label="Road map of the South Wales region with a location pin"></div>
<div class="car" role="img" aria-label="Photograph of a silver classic saloon car"></div>

<div class="watermark" style="top:3810px">Valtorix Design Valtorix</div>

<!-- cta + footer -->
<footer class="footer">
  <svg class="abs" style="left:0;top:-40px" width="1200" height="80" viewBox="0 0 1200 80"><path d="M0 70 L120 30 L120 80 L0 80 Z M1080 30 L1200 -10 L1200 80 L1080 80 Z" fill="#1b1c20"/></svg>
</footer>
<div class="cta"></div>
<div class="cta-pic" role="img" aria-label="Render of a kart chassis with steering wheel"></div>
<h2 class="cta" style="background:none;left:543px;top:3972px;width:480px;height:auto;color:#fff;font-size:38px;line-height:42px;font-weight:700">Start Your Project with a Technical Review</h2>
<p class="cta-text">Tell us about your product or challenge, and we'll provide a clear next-step recommendation.</p>
<div class="btn light" style="left:548px;top:4104px;width:140px">Get Started<span class="dot"><svg viewBox="0 0 24 24"><path d="M5 12h14M13 6l6 6-6 6" stroke="#fff" stroke-width="3" fill="none"/></svg></span></div>

<div class="f-logo logo"><span class="mark"></span>valtorix</div>
<p class="f-about">We are a UK based design consultancy offering a comprehensive mechanical and product design service from initial concepts through to full volume production.</p>
<div class="vline" style="left:322px"></div>
<div class="vline" style="left:505px"></div>
<div class="vline" style="left:738px"></div>
<div class="vline" style="left:920px"></div>
<div class="f-col" style="left:377px"><h4>Main Links</h4><ul><li>Home</li><li>About Us</li><li>Services</li><li>Portfolio</li><li>Case studies</li></ul></div>
<div class="f-col contact" style="left:560px"><h4>Contact Us</h4><ul><li><span class="ci"><i></i></span>South Wales, UK.</li><li><span class="ci"><i></i></span>+44 (0) 7700 900418</li><li><span class="ci"><i></i></span><span style="color:#6f8dff">info@valtorix.design</span></li></ul></div>
<div class="f-col" style="left:775px"><h4>Services</h4><ul><li>Mechanical Design</li><li>Design Consultancy</li><li>3D Printing</li><li>Project Management</li><li>Design for Manufacture (DFM)</li><li>TIG Welding</li><li>Painting</li></ul></div>
<div class="f-col brands" style="left:959px"><h4>Popular Brands</h4><ul><li><span class="ci"><i></i></span>Feedline</li><li><span class="ci"><i></i></span>Vidstream</li><li><span class="ci"><i></i></span>Linkwork</li></ul></div>
<div class="f-rule"></div>
<p class="copyright">Copyright © 2025 Valtorix Design All Rights Reserved.</p>

</body>
</html>
```